TalbeckLabs needs a new rocket based website

We need a new website that will be based on our rocket ship logo. We develop innovative solutions for enterprises. We would like to see a design that when the pages scroll, the rocket launches and goes from launch through a journey, similar to how we approach our customer. We would like areas for "Who are we", "What can we do", "What have we done", "How can we help". http://www.talbecklabs.example.au is our current website

Target Market(s)

Government, Enterprise, Cloud

Industry/Entity Type

Software Service

Coding

Coded - Design and coding required

Number of Pages Required

2 page

Requirements
Must have
• We would like to see a design that when the pages scroll, the rocket launches and goes from launch through a journey, similar to how we approach our customer.
• Must have a home page and a detail page.
• Would like to see the logo/rocket animate in some way when you scroll through he page.

```html
<!DOCTYPE html>
<html lang="en">
<head>
<meta charset="utf-8">
<title>TalbeckLabs – Innovative Software Solutions</title>
<link href="https://fonts.googleapis.com/css2?family=Poppins:wght@400;500;600;700&display=swap" rel="stylesheet">
<style>
:root{
  --orange:#f47f1f;
  --orange-dark:#e06d10;
  --navy:#1f3f5c;
  --navy-deep:#173249;
  --ink:#2b2b2b;
  --text:#3a3a3a;
  --muted:#666;
  --topbar:#f3f3f3;
  --white:#fff;
  --footer:#2a2a2a;
}
*{box-sizing:border-box;margin:0;padding:0}
html,body{width:1200px;height:3409px;overflow:hidden}
body{position:relative;font-family:"Poppins",sans-serif;color:var(--text);background:var(--white)}
.abs{position:absolute}

/* top bar */
.topbar{left:0;top:0;width:1200px;height:50px;background:var(--topbar);font-size:14px;color:#555}
.topbar .left{left:115px;top:15px;display:flex;gap:28px}
.topbar .right{right:115px;top:15px;display:flex;gap:26px}
.topbar span{display:flex;align-items:center;gap:8px}
.topbar svg{width:13px;height:13px;fill:#555}

/* header */
.header{left:0;top:50px;width:1200px;height:87px;background:var(--white)}
.brand{left:115px;top:22px;display:flex;align-items:center;gap:10px;font-weight:600;font-size:34px;color:var(--orange)}
.brand .dot{width:14px;height:14px;border-radius:50%;background:var(--orange)}
.nav{right:115px;top:32px;display:flex;gap:36px;font-size:16px;color:#222}

/* hero (children positioned relative to the hero box) */
.hero{left:0;top:137px;width:1200px;height:681px;background:linear-gradient(180deg,#244a6c 0%,var(--navy) 55%,#2c5374 100%);overflow:hidden}
.hero .clouds{left:-40px;bottom:-80px;width:1280px;height:250px;border-radius:50% 50% 0 0/60% 60% 0 0;background:linear-gradient(180deg,#f6f1e6,#fdfbf6);z-index:1}
.hero .rocket{left:600px;top:60px;width:500px;height:380px;border-radius:200px 40px 200px 40px;background:linear-gradient(135deg,#e2493a 0%,#cfd6d8 40%,#f7b52a 75%,rgba(247,181,42,0) 100%);opacity:.85;transform:rotate(-8deg)}
.hero .title{left:0;width:1200px;top:288px;text-align:center;color:var(--white);font-size:42px;font-weight:600;letter-spacing:3px;z-index:2}
.hero .sub{left:0;width:1200px;top:358px;text-align:center;color:var(--white);font-size:23px;font-weight:600;z-index:2}
.btn{display:inline-flex;align-items:center;justify-content:center;gap:10px;background:var(--orange);color:var(--white);border-radius:30px;font-size:17px;font-weight:500}
.hero .b1{left:391px;top:415px;width:215px;height:56px;z-index:2}
.hero .b2{left:620px;top:415px;width:190px;height:56px;z-index:2}
.btn svg{width:16px;height:16px;fill:var(--white)}
.follow{left:48px;top:380px;display:flex;flex-direction:column;gap:28px;align-items:center}
.follow i{display:block;width:10px;height:10px;border-radius:50%;background:var(--white)}
.follow .line{width:1px;height:40px;background:rgba(255,255,255,.7)}
.follow-label{left:22px;top:640px;color:var(--white);font-size:14px;transform:rotate(-90deg);transform-origin:left top}
.dots{left:1143px;top:463px;display:flex;flex-direction:column;gap:14px;align-items:center}
.dots i{display:block;width:10px;height:10px;border-radius:50%;background:rgba(255,255,255,.6)}
.dots i.on{width:24px;height:24px;border:3px solid var(--white);background:radial-gradient(circle,var(--white) 35%,transparent 40%)}

/* journey path */
.path{left:0;top:780px;width:1200px;height:2260px;pointer-events:none;z-index:3}
.hexmark{width:36px;height:40px;z-index:4}

/* headings */
.h-sec{left:0;width:1200px;text-align:center;color:var(--orange);font-size:33px;font-weight:600}

/* services */
.card{width:328px;height:223px;background:var(--white);box-shadow:0 2px 10px rgba(0,0,0,.12);text-align:center}
.card .icon{position:absolute;left:132px;top:-18px;width:64px;height:72px}
.card h3{margin-top:72px;color:var(--orange);font-size:21px;font-weight:600}
.card p{margin:10px auto 0;width:270px;font-size:14.5px;line-height:31px;color:#333}
.card a{display:block;margin-top:14px;font-size:15px;font-weight:600;color:var(--orange);text-decoration:none}

/* who */
.who{left:0;top:1323px;width:1200px;height:523px;background:linear-gradient(120deg,#3a3a3c 0%,#2d2e31 50%,#46474a 100%)}
.who h2{position:absolute;left:98px;top:105px;color:var(--white);font-size:33px;font-weight:600}
.who p{position:absolute;left:98px;top:165px;width:560px;color:#eee;font-size:16.5px;line-height:31.5px}
.who .photo{left:682px;top:86px;width:405px;height:353px}

/* work */
.work{width:307px;height:282px;background:var(--white);box-shadow:0 2px 10px rgba(0,0,0,.2);padding:7px}
.work .img{width:293px;height:230px;background:linear-gradient(135deg,#6f8aa3,#c7d2dc)}
.work .label{position:absolute;left:7px;bottom:7px;width:293px;height:46px;background:#1c1c1c;color:var(--white);font-size:20px;font-weight:600;display:flex;align-items:center;justify-content:center}
.more{left:518px;top:2359px;width:166px;height:50px;font-size:15px;font-weight:600}

/* help */
.help{left:0;top:2494px;width:1200px;height:506px;background:linear-gradient(120deg,#e9892e 0%,#f1954a 50%,#d9781f 100%)}
.help h2{position:absolute;left:0;width:1200px;top:44px;text-align:center;color:var(--white);font-size:33px;font-weight:600}
.help .intro{position:absolute;left:170px;width:860px;top:106px;text-align:center;color:var(--white);font-size:14.5px;line-height:30px}
.field{position:absolute;height:38px;background:var(--white);font-size:11.5px;color:#555;padding:10px 16px}
.field.msg{height:147px}
.submit{left:519px;top:2906px;width:166px;height:52px;background:var(--white);border-radius:30px;color:var(--ink);font-weight:600;font-size:18px;display:flex;align-items:center;justify-content:center}

/* footer */
.footer{left:0;top:3000px;width:1200px;height:409px;background:var(--footer);color:var(--white)}
.footer .fbrand{position:absolute;left:0;width:1200px;top:78px;display:flex;justify-content:center;align-items:center;gap:12px;font-size:44px;font-weight:600;color:var(--orange)}
.footer .fbrand .dot{width:18px;height:18px;border-radius:50%;background:var(--orange)}
.footer .contact{position:absolute;left:0;width:1200px;top:180px;display:flex;justify-content:center;gap:38px;font-size:15.5px}
.footer .contact span{display:flex;align-items:center;gap:9px}
.footer .contact svg{width:15px;height:15px;fill:var(--white)}
.footer .social{position:absolute;left:0;width:1200px;top:233px;display:flex;justify-content:center;gap:14px}
.footer .social i{display:block;width:41px;height:41px;border-radius:50%;background:var(--orange)}
.footer .links{position:absolute;left:0;width:1200px;top:306px;display:flex;justify-content:center;gap:12px;font-size:15.5px}
.footer .copy{position:absolute;left:0;width:1200px;top:354px;text-align:center;font-size:14.5px}
</style>
</head>
<body>

<div class="abs topbar">
  <div class="abs left">
    <span><svg viewBox="0 0 24 24"><path d="M6.6 10.8a15.1 15.1 0 0 0 6.6 6.6l2.2-2.2c.3-.3.7-.4 1-.2 1.1.4 2.3.6 3.6.6.6 0 1 .4 1 1V20c0 .6-.4 1-1 1A17 17 0 0 1 3 4c0-.6.4-1 1-1h3.5c.6 0 1 .4 1 1 0 1.3.2 2.5.6 3.6.1.3 0 .7-.2 1z"/></svg>Call: 1300 555 014</span>
    <span><svg viewBox="0 0 24 24"><path d="M2 5h20v14H2zm2 2v.5l8 5 8-5V7z"/></svg>Email: info@talbecklabs.example.au</span>
  </div>
  <div class="abs right">
    <span><svg viewBox="0 0 24 24"><circle cx="12" cy="12" r="10" fill="none" stroke="#555" stroke-width="2"/><circle cx="12" cy="10" r="3"/></svg>Login/ Register</span>
    <span><svg viewBox="0 0 24 24"><circle cx="12" cy="12" r="10"/></svg>Language</span>
  </div>
</div>

<header class="abs header">
  <div class="abs brand"><span class="dot"></span>TalbeckLabs</div>
  <nav class="abs nav"><span>Home</span><span>About</span><span>Our Services</span><span>Blog</span><span>Contact us</span></nav>
</header>

<section class="abs hero">
  <div class="abs rocket" role="img" aria-label="Illustration of a red and white rocket launching through the clouds"></div>
  <div class="abs clouds" role="img" aria-label="Soft white clouds"></div>
  <h1 class="abs title">TALBECKLABS</h1>
  <p class="abs sub">Innovative Software Solutions</p>
  <span class="abs btn b1"><svg viewBox="0 0 24 24"><circle cx="12" cy="12" r="9"/></svg>Find Out More</span>
  <span class="abs btn b2"><svg viewBox="0 0 24 24"><path d="M22 2 2 10l8 3 3 8z"/></svg>Contact us</span>
</section>
<div class="abs follow"><i></i><i></i><i></i><i></i><span class="line"></span></div>
<div class="abs follow-label">Follow us</div>
<div class="abs dots"><i></i><i class="on"></i><i></i></div>

<svg class="abs path" viewBox="0 0 1200 2260" fill="none" stroke="#f47f1f" stroke-width="2" stroke-dasharray="6 6">
  <path d="M560 40 C 420 60, 350 160, 370 250"/>
  <path d="M360 420 C 360 500, 500 540, 600 558"/>
  <path d="M600 560 C 720 540, 800 600, 800 700"/>
  <path d="M600 1066 C 400 1080, 270 1130, 260 1230"/>
  <path d="M270 1530 C 300 1640, 480 1700, 600 1710"/>
  <path d="M760 1740 C 880 1800, 880 1950, 800 2050 C 740 2130, 650 2180, 600 2220"/>
</svg>
<svg class="abs hexmark" style="left:582px;top:1300px" viewBox="0 0 36 40"><polygon points="18,0 36,10 36,30 18,40 0,30 0,10" fill="#f47f1f"/></svg>
<svg class="abs hexmark" style="left:582px;top:1826px" viewBox="0 0 36 40"><polygon points="18,0 36,10 36,30 18,40 0,30 0,10" fill="#f47f1f"/></svg>
<svg class="abs hexmark" style="left:582px;top:2474px" viewBox="0 0 36 40"><polygon points="18,0 36,10 36,30 18,40 0,30 0,10" fill="#f47f1f"/></svg>
<svg class="abs hexmark" style="left:582px;top:2980px" viewBox="0 0 36 40"><polygon points="18,0 36,10 36,30 18,40 0,30 0,10" fill="#f47f1f"/></svg>

<h2 class="abs h-sec" style="top:900px">WHAT CAN WE DO</h2>

<div class="abs card" style="left:98px;top:1016px">
  <svg class="icon" viewBox="0 0 64 72"><polygon points="32,1 63,18 63,54 32,71 1,54 1,18" fill="#fff" stroke="#eee" stroke-width="2"/><g fill="none" stroke="#f47f1f" stroke-width="2.5"><path d="M18 30l14-7 14 7-14 7z"/><path d="M18 37l14 7 14-7"/><path d="M18 44l14 7 14-7"/></g></svg>
  <h3>E-PARLIAMENT</h3>
  <p>All of your Parliamentary software and business process needs.</p>
  <a>Read More &#8594;</a>
</div>
<div class="abs card" style="left:436px;top:1016px">
  <svg class="icon" viewBox="0 0 64 72"><polygon points="32,1 63,18 63,54 32,71 1,54 1,18" fill="#fff" stroke="#eee" stroke-width="2"/><g fill="none" stroke="#f47f1f" stroke-width="2.5"><path d="M22 38a7 7 0 0 1 2-13 9 9 0 0 1 17 0 7 7 0 0 1 1 13z"/><path d="M32 38v10M26 48h12"/></g></svg>
  <h3>CLOUD</h3>
  <p>Cloud Office Suites, Migration, Security, Customisations.</p>
  <a>Read More &#8594;</a>
</div>
<div class="abs card" style="left:775px;top:1016px">
  <svg class="icon" viewBox="0 0 64 72"><polygon points="32,1 63,18 63,54 32,71 1,54 1,18" fill="#fff" stroke="#eee" stroke-width="2"/><g fill="none" stroke="#f47f1f" stroke-width="2.5"><rect x="20" y="24" width="24" height="24"/><path d="M24 44l8-10 5 5 6-9"/></g></svg>
  <h3>ARCHITECTURE &amp; DESIGN</h3>
  <p>Business process design, technology strategy and architecture.</p>
  <a>Read More &#8594;</a>
</div>

<section class="abs who" role="img" aria-label="Team meeting around an office table, darkened">
  <h2>WHO ARE WE</h2>
  <p>Offering the latest in enterprise architecture, design and development of bespoke software solutions<br>Always researching and implementing the latest technology for customers.<br>Sed ut perspiciatis unde omnis iste natus error sit voluptatem accusantium doloremque laudantium, totam rem aperiam, eaque ipsa quae ab illo inventore veritatis et quasi architecto beatae vitae dicta sunt explicabo.</p>
  <svg class="abs photo" viewBox="0 0 405 353" role="img" aria-label="Photo of a businesswoman presenting in a bright meeting room">
    <defs><linearGradient id="ph" x1="0" y1="0" x2="1" y2="1"><stop offset="0" stop-color="#d9dfe3"/><stop offset="1" stop-color="#7c8790"/></linearGradient></defs>
    <polygon points="101,2 304,2 403,176 304,351 101,351 2,176" fill="none" stroke="#f47f1f" stroke-width="3"/>
    <polygon points="112,18 293,18 383,176 293,335 112,335 22,176" fill="url(#ph)" stroke="#fff" stroke-width="4"/>
  </svg>
</section>

<h2 class="abs h-sec" style="top:1952px">WHAT HAVE WE DONE</h2>
<div class="abs work" style="left:102px;top:2041px"><div class="img" role="img" aria-label="Photo of a man at a digital display"></div><div class="label">SED UT PERSPICIATIS</div></div>
<div class="abs work" style="left:448px;top:2041px"><div class="img" role="img" aria-label="Photo of colleagues working at a laptop" style="background:linear-gradient(135deg,#b9c2c8,#5d6870)"></div><div class="label">SED UT PERSPICIATIS</div></div>
<div class="abs work" style="left:793px;top:2041px"><div class="img" role="img" aria-label="Photo of hands reviewing charts on paper" style="background:linear-gradient(135deg,#e6ecf2,#8ea6c4)"></div><div class="label">SED UT PERSPICIATIS</div></div>
<span class="abs btn more">VIEW MORE</span>

<section class="abs help" role="img" aria-label="Office team at work, tinted orange">
  <h2>HOW CAN WE HELP</h2>
  <p class="intro">Sed ut perspiciatis unde omnis iste natus error sit voluptatem accusantium doloremque laudantium, totam rem aperiam, eaque ipsa quae ab illo inventore veritatis et quasi architecto beatae vitae dicta sunt explicabo.</p>
  <div class="field" style="left:164px;top:188px;width:427px">First Name</div>
  <div class="field" style="left:609px;top:188px;width:430px">Last Name</div>
  <div class="field" style="left:164px;top:243px;width:427px">Company Name</div>
  <div class="field msg" style="left:609px;top:243px;width:430px">Message :</div>
  <div class="field" style="left:164px;top:297px;width:427px">Email Address</div>
  <div class="field" style="left:164px;top:352px;width:427px">Phone Number</div>
</section>
<span class="abs submit">Submit</span>

<footer class="abs footer">
  <div class="fbrand"><span class="dot"></span>TalbeckLabs</div>
  <div class="contact">
    <span><svg viewBox="0 0 24 24"><path d="M22 2 2 10l8 3 3 8z"/></svg>Unit 7, 48 Corella St, Marden, SA 5070</span>
    <span><svg viewBox="0 0 24 24"><path d="M6.6 10.8a15.1 15.1 0 0 0 6.6 6.6l2.2-2.2c.3-.3.7-.4 1-.2 1.1.4 2.3.6 3.6.6.6 0 1 .4 1 1V20c0 .6-.4 1-1 1A17 17 0 0 1 3 4c0-.6.4-1 1-1h3.5c.6 0 1 .4 1 1 0 1.3.2 2.5.6 3.6.1.3 0 .7-.2 1z"/></svg>Phone: 1300 555 014</span>
    <span><svg viewBox="0 0 24 24"><path d="M2 5h20v14H2zm2 2v.5l8 5 8-5V7z"/></svg>Email: info@talbecklabs.example.au</span>
  </div>
  <div class="social"><i></i><i></i><i></i><i></i><i></i></div>
  <div class="links"><span>Home</span><span>|</span><span>About</span><span>|</span><span>Our Services</span><span>|</span><span>Our Blog</span><span>|</span><span>Contact us</span><span>|</span><span>Terms of use</span><span>|</span><span>Privacy Policy</span></div>
  <div class="copy">Copyright © 2018. All Rights Reserved.</div>
</footer>

</body>
</html>
```